Make a CV more classy for an orthopaedic hand surgeon

I actually don't want a resume with many pictures etc. I want a CV that is classy, and would be attractive to lawyers. I want you to keep the same content in my current CV just rearrange things if necessary and make it nice, with nice headers and organization. Again, like the sleek, classy, luxury, but professional look. I want lawyers and other recruiters to look at my CV and know I am high class

Target Market(s)

Lawyers, Consulting gigs--they want to see that I am smart and have a lot of accolades

Industry/Entity Type

Medicine

Colors
0054AA
0677BA
7BADD7
CADEEF
E8F1F8

Requirements
Must have
• Classy, luxury, professional
Nice to have
• NA
Should not have
• Additional photos, resume-type look--bubbles everywhere, boxes circled. Should look like the format it is in already, just spiced up and organized better with nice fancy headers and sleek look

```html
<!DOCTYPE html>
<html lang="en">
<head>
<meta charset="utf-8">
<title>Celia Marlowe, M.D. — Curriculum Vitae</title>
<link rel="stylesheet" href="https://fonts.googleapis.com/css2?family=Montserrat:wght@400;500;600;700;800&display=swap">
<style>
  :root {
    --backdrop: #4a4a4a;
    --paper: #ffffff;
    --ink: #141414;
    --ink-soft: #555555;
    --bar: #111111;
    --gold-light: #ecd9a8;
    --gold-mid: #dcc080;
    --gold-deep: #c6a458;
    --rule: #3a3a3a;
  }
  * { box-sizing: border-box; margin: 0; padding: 0; }
  html, body {
    width: 1200px; height: 1200px; overflow: hidden;
    background: var(--backdrop);
    font-family: "Montserrat", sans-serif;
    color: var(--ink);
  }
  .page {
    position: absolute; left: 204px; top: 40px;
    width: 792px; height: 1120px;
    background: var(--paper);
    display: flex;
    overflow: hidden;
  }
  .side { width: 300px; flex: none; }
  .main { flex: 1; padding: 34px 28px 0 26px; }

  .identity {
    height: 620px;
    background: linear-gradient(160deg, var(--gold-light) 0%, var(--gold-mid) 50%, var(--gold-deep) 100%);
    border-bottom-right-radius: 30px;
    padding: 96px 30px 0 36px;
  }
  .practice-name { font-weight: 700; font-size: 16px; letter-spacing: .12em; margin-bottom: 40px; }
  .person-name { font-weight: 800; font-size: 34px; line-height: 1.08; letter-spacing: .02em; }
  .person-title { margin-top: 14px; font-weight: 700; font-size: 10px; line-height: 1.35; letter-spacing: .03em; }
  .person-rule { height: 1.5px; background: var(--rule); margin: 22px 0 26px; }
  .contact { display: grid; grid-template-columns: 62px 1fr; row-gap: 8px; font-size: 9.5px; }
  .contact dt { font-weight: 700; }
  .contact dd { color: #3a3a3a; line-height: 1.35; }

  .side-sections { padding: 28px 24px 0 36px; }

  .section { margin-bottom: 20px; }
  .section-bar {
    background: var(--bar); color: #fff;
    font-weight: 500; font-size: 10.5px; letter-spacing: .05em;
    text-transform: uppercase; line-height: 1.3;
    padding: 6px 12px; border-radius: 6px; margin-bottom: 10px;
  }
  .entry { position: relative; padding-left: 14px; margin-bottom: 8px; font-size: 9.5px; line-height: 1.4; }
  .entry::before {
    content: ""; position: absolute; left: 0; top: 4px;
    width: 5px; height: 5px; border-radius: 50%; background: var(--gold-deep);
  }
  .entry-date { font-weight: 700; color: var(--ink); }
  .entry-role { font-weight: 700; }
  .entry-text { color: var(--ink-soft); }

  .timeline { display: grid; grid-template-columns: 92px 1fr; row-gap: 6px; font-size: 9.5px; line-height: 1.4; }
  .timeline .year { position: relative; padding-left: 14px; font-weight: 700; }
  .timeline .year::before {
    content: ""; position: absolute; left: 0; top: 4px;
    width: 5px; height: 5px; border-radius: 50%; background: var(--gold-deep);
  }
  .timeline .year::after {
    content: ""; position: absolute; left: 70px; top: 7px;
    width: 14px; height: 1px; background: var(--gold-mid);
  }
  .timeline .detail { color: var(--ink-soft); }

  .foot-band {
    position: absolute; left: 0; bottom: 0;
    width: 380px; height: 30px;
    background: linear-gradient(90deg, var(--gold-deep), var(--gold-mid));
    border-top-right-radius: 30px;
  }
</style>
</head>
<body>
<div class="page">
  <aside class="side">
    <header class="identity">
      <p class="practice-name">ARDENT SURGICAL</p>
      <h1 class="person-name">CELIA<br>MARLOWE, M.D.</h1>
      <p class="person-title">BOARD CERTIFIED,<br>HAND SUBSPECIALTY CERTIFIED</p>
      <div class="person-rule"></div>
      <dl class="contact">
        <dt>ADDRESS:</dt><dd>4820 Harbor Lane, Suite 110,<br>Weston Park, FL 33000</dd>
        <dt>PHONE:</dt><dd>555-014-2200</dd>
        <dt>FAX:</dt><dd>555-014-2201</dd>
        <dt>CELL:</dt><dd>555-018-3390</dd>
      </dl>
    </header>

    <div class="side-sections">
      <section class="section">
        <h2 class="section-bar">Education:</h2>
        <div class="entry"><span class="entry-date">Aug/2005 - May/2009</span><br><span class="entry-text">BS - Ashcombe University</span></div>
        <div class="entry"><span class="entry-date">Aug/2009 - May/2013</span><br><span class="entry-text">MD - Halbrook University School of Medicine and Dentistry</span></div>
      </section>

      <section class="section">
        <h2 class="section-bar">Post-Graduate Training and Fellowship Appointments:</h2>
        <div class="entry"><span class="entry-date">Jun/2013 - Jul/2018</span><br><span class="entry-role">Resident in Orthopaedic Surgery</span><br><span class="entry-text">Northvale Hospital, Northvale</span></div>
        <div class="entry"><span class="entry-date">Aug/2018 - Jul/2019</span><br><span class="entry-role">Fellow in Hand Surgery</span><br><span class="entry-text">Hospital of Eastmoor University, Philadelphia</span></div>
      </section>

      <section class="section">
        <h2 class="section-bar">Employment History:</h2>
        <div class="entry"><span class="entry-date">Sep/2019 - Sep/2021</span><br><span class="entry-role">Hand &amp; Upper Extremity Orthopaedic Surgeon,</span> <span class="entry-text">Meridian Health Partners Medical Group, Atlanta GA</span></div>
        <div class="entry"><span class="entry-date">Oct/2021 - Present</span><br><span class="entry-role">Hand &amp; Upper Extremity Orthopaedic Surgeon,</span> <span class="entry-text">Owner, Ardent Upper Extremity Surgery PLLC</span></div>
      </section>
    </div>
  </aside>

  <main class="main">
    <section class="section">
      <h2 class="section-bar">Board Certification:</h2>
      <div class="entry"><span class="entry-date">Nov/2021 – Present</span><br><span class="entry-text">Federal Board of Orthopaedic Surgery (FBOS),<br>Certified in Orthopaedic Surgery</span></div>
      <div class="entry"><span class="entry-date">Aug/2022</span><br><span class="entry-text">FBOS, Certified in Surgery of the Hand</span></div>
    </section>

    <section class="section">
      <h2 class="section-bar">Memberships in Professional and Scientific Societies:</h2>
      <div class="timeline">
        <span class="year">2019</span><span class="detail">GHS Member</span>
        <span class="year">2016</span><span class="detail">GHS Resident Candidate Member</span>
        <span class="year">2015</span><span class="detail">Resident member, OrthoTrauma Forum</span>
        <span class="year">2013</span><span class="detail">Resident Member, Northvale Hospital Minority Housestaff Organization</span>
        <span class="year">2013</span><span class="detail">Resident Member, Collegium of Orthopaedic Surgeons</span>
        <span class="year">2009</span><span class="detail">Student Physicians Alliance (SPA)</span>
      </div>
    </section>

    <section class="section">
      <h2 class="section-bar">Awards, Honors and Membership in Honorary Societies:</h2>
      <div class="entry"><span class="entry-date">2019 - 2021</span><br><span class="entry-text">6-time “Standout Provider of the Month” Award Recipient at Meridian Health Partners</span></div>
      <div class="entry"><span class="entry-date">2016</span><br><span class="entry-text">Recipient, Arthur L. Wren Guild of Hand Surgeons (GHS) Scholarship</span></div>
      <div class="entry"><span class="entry-date">2016 NEW</span><br><span class="entry-text">Appointed to Graduate Medical Education Committee (GMEC), Northvale Hospital</span></div>
      <div class="entry"><span class="entry-date">2013</span><br><span class="entry-text">Northvale School of Medicine Excellent Teaching Resident Award</span></div>
      <div class="entry"><span class="entry-date">2009</span><br><span class="entry-text">Lindell Fellowship Scholarship Recipient, Halbrook University School of Medicine and Dentistry</span></div>
      <div class="entry"><span class="entry-date">2006 - 2009</span><br><span class="entry-text">Dean’s List, Ashcombe University</span></div>
      <div class="entry"><span class="entry-date">2005</span><br><span class="entry-text">Coastal Racquet League (CRL) Marcus Bell Scholarship Recipient</span></div>
      <div class="entry"><span class="entry-date">2005</span><br><span class="entry-text">Key-Note Speaker, Harbor Cup Tennis Championship Opening Night Gala</span></div>
    </section>

    <section class="section">
      <h2 class="section-bar">Leadership, Mentorship, and Work Experience:</h2>
      <div class="timeline">
        <span class="year">2022</span><span class="detail">Physician Panelist, Growing Roots: Surgical Careers Edition, 2022 SPA Annual Medical Education Conference (AMEC), Orlando, FL</span>
        <span class="year">2016-2018</span><span class="detail">Resident Representative, Graduate Medical Education Committee (GMEC), Northvale Hospital</span>
        <span class="year">2015-2018</span><span class="detail">Instructor, Musculoskeletal Workshops, Northvale School of Medicine</span>
        <span class="year">2015</span><span class="detail">Assistant-coordinator/Instructor, Physician Assistant Orthopaedic Maneuvers Workshops, Northvale School of Medicine</span>
        <span class="year">2015</span><span class="detail">Co-coordinator/Presenter, Allied Physicians Guild (APG) Middle School Premedical Education Day</span>
      </div>
    </section>
  </main>

  <div class="foot-band"></div>
</div>
</body>
</html>
```